Redesign This Psychology Website

We would like a slight redesign of this successful psychology (relationship counselling) website:

www.TheKelvaleClinic.com.au

We are updating the website, and we'd like a slight refresh of the design and style.

Please keep to very similar colours, and use the same logo. We're looking for around 10 page templates, however the main one is the home page.

Keep in mind, this website already converts quite well, so we want a new, fresh design in keeping with this one. Please don't bother designing something too extremely different.

thanks :)

Target Market(s)

couples who are looking for relationship counselling. Men and women, 25 - 70, across Australia

Industry/Entity Type

Psychology

Number of Pages Required

5+ page

Font styles to use
Sans Serif

Colors
87cfc6
b7a5cd
ec1f27
ffffff
cee9f5

Requirements
Must have
• a similar look to the current design, just looking for a slight refresh.
• Search bar
• Areas for lots of photos
• same logo
• lots of content areas
Nice to have
• great content areas, where we can display a lot of content and our areas.
Should not have
• no colors like orange, etc.
• should not have a totally different feel.

```html
<!DOCTYPE html>
<html lang="en">
<head>
<meta charset="utf-8">
<title>The Kelvale Clinic – Relationship &amp; Marriage Counselling</title>
<link href="https://fonts.googleapis.com/css2?family=Open+Sans:ital,wght@0,400;0,600;0,700;1,700;1,800&display=swap" rel="stylesheet">
<style>
:root{
  --teal:#87cfc6;
  --teal-dark:#2d8c96;
  --purple:#b7a5cd;
  --purple-dark:#9d88bb;
  --red:#ec1f27;
  --sky:#cee9f5;
  --ink:#333;
  --muted:#777;
  --line:#ddd;
  --pale:#f2f2f2;
  --footer:#2f2f2f;
  --white:#fff;
}
*{box-sizing:border-box;margin:0;padding:0}
html,body{width:1200px;height:3557px;overflow:hidden}
body{font-family:"Open Sans",Arial,sans-serif;color:var(--ink);background:var(--white);font-size:13px;line-height:1.5}
.wrap{width:940px;margin:0 auto;position:relative}
a{color:inherit;text-decoration:none}

/* header */
.site-header{height:130px}
.brand{position:absolute;left:0;top:30px;display:flex;align-items:center;gap:12px}
.brand-dot{width:50px;height:50px;border-radius:50%;background:var(--teal)}
.brand-name{font-size:28px;font-weight:600;color:var(--teal-dark);line-height:1}
.brand-tag{position:absolute;left:62px;top:88px;font-size:10px;color:var(--muted);white-space:nowrap}
.header-call{position:absolute;left:515px;top:38px;font-size:14px;color:#555;display:flex;align-items:center;gap:6px}
.search{position:absolute;right:0;top:30px;width:200px;height:40px;border:1px solid var(--line);display:flex;align-items:center;justify-content:space-between;padding:0 12px;font-size:12px;color:#999}
.main-nav{position:absolute;right:0;top:88px;display:flex;gap:26px;font-size:13px;color:#444}
.main-nav .active{color:var(--red)}

.sub-nav{height:41px;background:var(--purple)}
.sub-nav ul{list-style:none;display:flex;height:41px;font-size:12.5px;font-weight:600;color:var(--white);text-transform:uppercase}
.sub-nav li{padding:0 28px;display:flex;align-items:center}
.sub-nav li.current{background:var(--purple-dark)}

/* hero */
.hero{height:444px;position:relative;background:linear-gradient(180deg,#c9d6de 0%,#e7e4dc 45%,#cbb9a0 100%)}
.hero-photo{position:absolute;inset:0}
.hero-copy{position:absolute;left:130px;top:120px;width:600px}
.hero-copy h1{font-size:24px;font-weight:400;color:var(--teal-dark);margin-bottom:14px}
.hero-copy p{font-size:12.5px;color:#444;margin-bottom:16px}
.btn-light{display:inline-block;background:var(--white);color:#555;font-size:11px;padding:8px 14px}
.hero-dots{position:absolute;left:565px;top:405px;display:flex;gap:6px;background:rgba(0,0,0,.25);padding:5px 8px;border-radius:10px}
.hero-dots span{width:8px;height:8px;border-radius:50%;background:var(--white)}

/* services */
.services{padding:55px 0 40px}
.service-grid{display:grid;grid-template-columns:repeat(4,220px);gap:20px}
.service-photo{height:160px}
.service h2{font-size:17px;line-height:1.15;font-weight:600;color:var(--red);text-transform:uppercase;margin:10px 0 8px;height:46px}
.service p{font-size:10.5px;color:#555;line-height:1.45;height:48px}
.service p b{color:var(--ink)}
.btn-outline{display:block;border:1px solid #ccc;height:38px;line-height:36px;text-align:center;font-size:12px;color:#555;margin-top:14px}
.premarriage{width:220px;margin-top:10px}

/* finder */
.finder{height:320px;display:flex}
.finder-form{width:600px;background:var(--teal);padding:60px 0 0 130px;color:var(--white)}
.finder-form h2{font-size:19px;font-weight:600;margin-bottom:10px}
.field-row{display:flex;gap:16px;align-items:flex-end}
.field label{display:block;font-size:11px;margin:4px 0 3px}
.field .input{height:40px;background:var(--white);color:#999;font-size:11px;padding:0 10px;display:flex;align-items:center;justify-content:space-between}
.btn-dark{background:#3a3a3a;color:var(--white);font-size:12px;font-weight:600;height:40px;padding:0 14px;display:flex;align-items:center}
.finder-info{flex:1;background:#f3f3f3;padding:55px 130px 0 30px}
.finder-info h2{font-size:24px;font-weight:400;color:var(--teal-dark);margin-bottom:14px}
.finder-info p{font-size:11.5px;color:#555;margin-bottom:12px}

/* issues */
.issues{height:365px;padding-top:58px}
.issues h2{text-align:center;font-size:16px;font-weight:600;color:var(--teal-dark);margin-bottom:20px}
.issue-list{display:grid;grid-template-columns:310px 390px 240px;row-gap:8px;list-style:none;font-size:12px;color:#555;grid-auto-flow:column;grid-template-rows:repeat(6,24px)}
.issue-list li{display:flex;align-items:center;gap:10px;white-space:nowrap}

/* blog */
.blog{height:560px;background:#f2f2f2;padding-top:85px}
.blog-head{display:flex;justify-content:space-between;align-items:center;margin-bottom:20px}
.blog-head h2{font-size:24px;font-weight:400;color:var(--teal-dark)}
.arrows{display:flex;gap:6px}
.arrows span{width:22px;height:22px;border:1px solid #999;display:flex;align-items:center;justify-content:center}
.blog-grid{display:grid;grid-template-columns:repeat(3,300px);gap:20px}
.post-photo{height:192px}
.post time{display:block;font-size:12px;color:#666;margin:22px 0 8px}
.post h3{font-size:13px;font-weight:600;line-height:1.4;margin-bottom:10px}
.post p{font-size:10.5px;color:#888;line-height:1.5}

/* topic tiles */
.topics{padding-top:85px;height:975px}
.tile-grid{display:grid;grid-template-columns:repeat(3,300px);gap:25px 20px}
.tile{height:215px;position:relative}
.tile span{position:absolute;left:16px;bottom:18px;right:16px;color:var(--white);font-size:14px;line-height:1.35}
.banner-row{display:grid;grid-template-columns:repeat(3,300px);gap:20px;margin-top:25px}
.promo{height:240px;position:relative;display:block}
.promo-photo{position:absolute;inset:0 0 26px 0}
.promo-title{position:absolute;left:6px;top:6px;font-size:25px;line-height:1.12;font-style:italic;font-weight:800;color:var(--red)}
.promo-title.dark{left:auto;right:8px;top:80px;color:#222;font-size:22px;text-align:left;width:150px}
.promo-bar{position:absolute;left:0;right:0;bottom:0;color:var(--white);font-size:14px;line-height:1.3;padding:3px 32px 3px 10px;display:block}
.promo-bar.red{background:var(--red);height:44px}
.promo-bar.teal{background:var(--teal-dark);height:26px;font-size:14.5px}
.promo-bar svg{position:absolute;right:8px;top:50%;transform:translateY(-50%)}
.rebates h3{font-size:19px;font-weight:700;color:var(--red);margin-bottom:4px;line-height:1.3}
.badges{display:grid;grid-template-columns:repeat(3,1fr);gap:6px;margin-bottom:6px}
.badges span{height:24px;border-radius:4px}
.more{text-align:center;color:var(--red);font-size:12px;border-top:1px solid var(--red);padding-top:2px;margin-bottom:4px}
.rebates p{font-size:16px;line-height:1.2;color:#666}
.rebates p b{color:var(--red)}

/* footer */
.site-footer{height:242px;background:var(--footer);color:#ccc;padding-top:40px}
.footer-grid{display:grid;grid-template-columns:270px 350px 220px 100px}
.site-footer h4{color:var(--white);font-size:15px;font-weight:600;margin-bottom:12px}
.email{width:220px;height:40px;background:var(--white);color:#555;font-size:11px;display:flex;align-items:center;justify-content:space-between;padding:0 12px}
.social{display:flex;gap:8px;margin-top:18px}
.social span{width:30px;height:30px;border-radius:50%;background:#777}
.links{display:grid;grid-template-columns:100px 200px;font-size:11px;list-style:none;line-height:1.75}
.links li::before{content:"› ";color:#888}
.contact{font-size:11px;line-height:1.7}
.contact div{display:flex;gap:8px}
.copy{font-size:10.5px;line-height:1.5}
</style>
</head>
<body>

<header class="site-header">
  <div class="wrap">
    <a class="brand" href="#"><span class="brand-dot"></span><span class="brand-name">The Kelvale Clinic</span></a>
    <span class="brand-tag">Helping you create loving relationships</span>
    <div class="header-call">
      <svg width="12" height="16" viewBox="0 0 12 16"><rect x="1" y="1" width="10" height="14" rx="2" fill="none" stroke="#555" stroke-width="1.6"/><circle cx="6" cy="12" r="1" fill="#555"/></svg>
      Call us on : 1300 555 019
    </div>
    <div class="search">Search
      <svg width="13" height="13" viewBox="0 0 13 13"><circle cx="5.5" cy="5.5" r="4" fill="none" stroke="#444" stroke-width="1.6"/><line x1="8.5" y1="8.5" x2="12" y2="12" stroke="#444" stroke-width="1.8"/></svg>
    </div>
    <nav class="main-nav">
      <a class="active" href="#">Home</a><a href="#">About</a><a href="#">Resources</a><a href="#">Blog</a><a href="#">Shop</a><a href="#">Cart</a><a href="#">Contact</a>
    </nav>
  </div>
</header>

<nav class="sub-nav">
  <div class="wrap">
    <ul>
      <li class="current">Counselling Types</li>
      <li>Relationship Counselling Locations</li>
      <li>Sex Theraphy Locations</li>
      <li>Quizzes</li>
      <li>FAQs</li>
    </ul>
  </div>
</nav>

<section class="hero">
  <div class="hero-photo" role="img" aria-label="Smiling couple walking hand in hand along a beach"></div>
  <div class="hero-copy">
    <h1>We Specialise in Relationship &amp; Marriage Counselling</h1>
    <p>At the Kelvale Clinic, we are a group of PSYCHOLOGISTS, Australia wide who are passionate about relationships and helping you with yours.</p>
    <p>Our vision is to provide the most highly regarded and comprehensive marriage counselling and relationship counselling, and sex therapy in Australia, at reasonable and affordable rates.</p>
    <a class="btn-light" href="#">Read more</a>
  </div>
  <div class="hero-dots"><span></span><span></span><span></span><span></span></div>
</section>

<section class="services">
  <div class="wrap">
    <div class="service-grid">
      <article class="service">
        <div class="service-photo" role="img" aria-label="Couple smiling together outdoors" style="background:linear-gradient(135deg,#a9b9c4,#d8c9b8)"></div>
        <h2>Relationship Counselling</h2>
        <p>Communication, Recovering from an affair, Loss of intimacy &amp; love, Power battles, Feeling like friends, not lovers. <b>More</b></p>
      </article>
      <article class="service">
        <div class="service-photo" role="img" aria-label="Older couple embracing and laughing" style="background:linear-gradient(135deg,#c7c9cc,#9ea3a8)"></div>
        <h2>Sex Therapy Counselling</h2>
        <p>Low libido, Erectile difficulties, Premature ejaculation, Differing libidos, Porn addiction, keeping sex exciting. <b>More</b></p>
      </article>
      <article class="service">
        <div class="service-photo" role="img" aria-label="Angry man in a suit shouting" style="background:linear-gradient(135deg,#5a3d2c,#a06a40)"></div>
        <h2>Anger Management Counselling</h2>
        <p>Managing angry outbursts, expressing your anger in healthy ways. <b>More</b></p>
      </article>
      <article class="service">
        <div class="service-photo" role="img" aria-label="Man looking at his reflected double" style="background:linear-gradient(135deg,#3b4a5a,#8c7a6a)"></div>
        <h2>Narcissism Counselling</h2>
        <p>Managing narcissistic, superior, entitled, arrogant and lack of empathy tendencies in you or your partner. <b>More</b></p>
      </article>
    </div>
    <div class="service-grid">
      <a class="btn-outline" href="#">Take our Relationship Quiz</a>
      <a class="btn-outline" href="#">Take our Sex Quiz</a>
      <a class="btn-outline" href="#">Take our Anger Test</a>
      <a class="btn-outline" href="#">Check your Narcissism Profile</a>
    </div>
    <a class="btn-outline premarriage" href="#">Pre-marriage</a>
  </div>
</section>

<section class="finder">
  <div class="finder-form">
    <h2>Find Our Psychologist Near You</h2>
    <div class="field-row">
      <div class="field" style="width:215px"><label>Type of Counselling</label>
        <div class="input">Select <svg width="8" height="5" viewBox="0 0 8 5"><path d="M0 0L4 5L8 0Z" fill="#999"/></svg></div></div>
      <div class="field" style="width:216px"><label>Location</label><div class="input"></div></div>
    </div>
    <div class="field-row">
      <div class="field" style="width:215px"><label>Postcode</label><div class="input"></div></div>
      <div class="btn-dark">SEARCH</div>
    </div>
  </div>
  <div class="finder-info">
    <h2>Our Kelvale Relationship Psychologists</h2>
    <p>Our team of 75 hand chosen Registered Psychologists in 81 locations Australia wide, are individually selected for their knowledge, experience, compassion, and unbiased approach to marriage counselling and sexual therapy.</p>
    <p>In addition all our Psychologists take part in our initial Relationship Counselling Methodologies Training and yearly in-house conferences, ensuring you are in safe and experienced hands.</p>
    <p>As we are Psychologists, you may be eligible for CareShield &amp; Private Health Insurance Rebates.<br>We are highly experienced and can help you with all kinds of relationship difficulties.</p>
  </div>
</section>

<section class="issues">
  <div class="wrap">
    <h2>Here are some of the common ones:</h2>
    <ul class="issue-list">
      <li><svg width="10" height="8" viewBox="0 0 10 8"><path d="M1 4L4 7L9 1" fill="none" stroke="#888" stroke-width="1.6"/></svg>Affairs</li>
      <li><svg width="10" height="8" viewBox="0 0 10 8"><path d="M1 4L4 7L9 1" fill="none" stroke="#888" stroke-width="1.6"/></svg>Controlling behaviour</li>
      <li><svg width="10" height="8" viewBox="0 0 10 8"><path d="M1 4L4 7L9 1" fill="none" stroke="#888" stroke-width="1.6"/></svg>Verbal abuse</li>
      <li><svg width="10" height="8" viewBox="0 0 10 8"><path d="M1 4L4 7L9 1" fill="none" stroke="#888" stroke-width="1.6"/></svg>Imbalance of power</li>
      <li><svg width="10" height="8" viewBox="0 0 10 8"><path d="M1 4L4 7L9 1" fill="none" stroke="#888" stroke-width="1.6"/></svg>Lack of intimacy</li>
      <li><svg width="10" height="8" viewBox="0 0 10 8"><path d="M1 4L4 7L9 1" fill="none" stroke="#888" stroke-width="1.6"/></svg>Poor communication</li>
      <li><svg width="10" height="8" viewBox="0 0 10 8"><path d="M1 4L4 7L9 1" fill="none" stroke="#888" stroke-width="1.6"/></svg>Loss of love</li>
      <li><svg width="10" height="8" viewBox="0 0 10 8"><path d="M1 4L4 7L9 1" fill="none" stroke="#888" stroke-width="1.6"/></svg>Relationship neglect</li>
      <li><svg width="10" height="8" viewBox="0 0 10 8"><path d="M1 4L4 7L9 1" fill="none" stroke="#888" stroke-width="1.6"/></svg>Sexual problems</li>
      <li><svg width="10" height="8" viewBox="0 0 10 8"><path d="M1 4L4 7L9 1" fill="none" stroke="#888" stroke-width="1.6"/></svg>Problems from childhood</li>
      <li><svg width="10" height="8" viewBox="0 0 10 8"><path d="M1 4L4 7L9 1" fill="none" stroke="#888" stroke-width="1.6"/></svg>Problems with parenting your children</li>
      <li><svg width="10" height="8" viewBox="0 0 10 8"><path d="M1 4L4 7L9 1" fill="none" stroke="#888" stroke-width="1.6"/></svg>Step children and in-laws</li>
      <li><svg width="10" height="8" viewBox="0 0 10 8"><path d="M1 4L4 7L9 1" fill="none" stroke="#888" stroke-width="1.6"/></svg>All forms of family problems</li>
      <li><svg width="10" height="8" viewBox="0 0 10 8"><path d="M1 4L4 7L9 1" fill="none" stroke="#888" stroke-width="1.6"/></svg>Anger management problems</li>
      <li><svg width="10" height="8" viewBox="0 0 10 8"><path d="M1 4L4 7L9 1" fill="none" stroke="#888" stroke-width="1.6"/></svg>Porn addiction problems</li>
      <li><svg width="10" height="8" viewBox="0 0 10 8"><path d="M1 4L4 7L9 1" fill="none" stroke="#888" stroke-width="1.6"/></svg>Pre-marriage programs</li>
      <li><svg width="10" height="8" viewBox="0 0 10 8"><path d="M1 4L4 7L9 1" fill="none" stroke="#888" stroke-width="1.6"/></svg>Narcissism problems</li>
    </ul>
  </div>
</section>

<section class="blog">
  <div class="wrap">
    <div class="blog-head">
      <h2>Blog</h2>
      <div class="arrows">
        <span><svg width="6" height="9" viewBox="0 0 6 9"><path d="M5 1L1 4.5L5 8" fill="none" stroke="#555" stroke-width="1.4"/></svg></span>
        <span><svg width="6" height="9" viewBox="0 0 6 9"><path d="M1 1L5 4.5L1 8" fill="none" stroke="#555" stroke-width="1.4"/></svg></span>
      </div>
    </div>
    <div class="blog-grid">
      <article class="post">
        <div class="post-photo" role="img" aria-label="Woman with arms outstretched on a sunny beach" style="background:linear-gradient(135deg,#e8e6df,#b9b2a4)"></div>
        <time>24 April, 2017</time>
        <h3>Simple daily habits that help couples stay close and feel heard.</h3>
        <p>Small moments of attention add up over time. Here we share easy ideas you can try at home this week together.</p>
      </article>
      <article class="post">
        <div class="post-photo" role="img" aria-label="Couple laughing together in a cafe" style="background:linear-gradient(135deg,#4f4a3a,#b58d5e)"></div>
        <time>24 April, 2017</time>
        <h3>Simple daily habits that help couples stay close and feel heard.</h3>
        <p>Small moments of attention add up over time. Here we share easy ideas you can try at home this week together.</p>
      </article>
      <article class="post">
        <div class="post-photo" role="img" aria-label="Psychologist talking with a client in an office" style="background:linear-gradient(135deg,#a7b3bd,#5d7d9c)"></div>
        <time>24 April, 2017</time>
        <h3>Simple daily habits that help couples stay close and feel heard.</h3>
        <p>Small moments of attention add up over time. Here we share easy ideas you can try at home this week together.</p>
      </article>
    </div>
  </div>
</section>

<section class="topics">
  <div class="wrap">
    <div class="tile-grid">
      <a class="tile" href="#" role="img" aria-label="Couple sitting apart in a car at sunset" style="background:linear-gradient(180deg,#a27c52,#3a2c22)"><span>How to deal with an affair?</span></a>
      <a class="tile" href="#" role="img" aria-label="Two women laughing together" style="background:linear-gradient(180deg,#c9ab7a,#4a3b2c)"><span>Same Sex Relationships &amp; Counselling</span></a>
      <a class="tile" href="#" role="img" aria-label="Couple arguing at home" style="background:linear-gradient(180deg,#7a8590,#2f3338)"><span>Are you living with a narcissist?</span></a>
      <a class="tile" href="#" role="img" aria-label="Thoughtful man with hands clasped" style="background:linear-gradient(180deg,#6d5c50,#241e1a)"><span>Is one of you an Intimacy Withholder?</span></a>
      <a class="tile" href="#" role="img" aria-label="Hands typing on a laptop" style="background:linear-gradient(180deg,#d8d6d2,#5a5753)"><span>Watching Porn: How normal is it? When is Porn an addiction?</span></a>
      <a class="tile" href="#" role="img" aria-label="Couple reading a tablet together" style="background:linear-gradient(180deg,#8f8a80,#2e2c28)"><span>Is your relationship safe? Is your partner controlling?</span></a>
    </div>

    <div class="banner-row">
      <a class="promo" href="#">
        <div class="promo-photo" role="img" aria-label="Worried woman holding her face" style="background:linear-gradient(90deg,#f4f1ee 40%,#d8b9a5)"></div>
        <div class="promo-title">Is Anxiety,<br>Depression<br>or Stress<br>bothering<br>YOU?</div>
        <div class="promo-bar red">Click here for <b>help</b> from Kelvale Anxiety &amp; Depression Psychologists
          <svg width="18" height="18" viewBox="0 0 18 18"><circle cx="9" cy="9" r="8" fill="#fff"/><path d="M7 5L11 9L7 13" fill="none" stroke="#ec1f27" stroke-width="2"/></svg></div>
      </a>
      <a class="promo" href="#">
        <div class="promo-photo" role="img" aria-label="Doctor and nurse smiling" style="background:linear-gradient(90deg,#c9d8e2,#eef2f4 60%)"></div>
        <div class="promo-title dark">Information for referring GPs &amp; health professionals</div>
        <div class="promo-bar teal">Click here for more details.
          <svg width="16" height="16" viewBox="0 0 16 16"><circle cx="8" cy="8" r="7" fill="#fff"/><path d="M6 4.5L9.5 8L6 11.5" fill="none" stroke="#2d8c96" stroke-width="2"/></svg></div>
      </a>
      <a class="promo rebates" href="#">
        <h3>Rebates Available</h3>
        <div class="badges">
          <span style="background:#1c9b3e"></span><span style="background:#c7e3f2"></span><span style="background:#2b7fcf"></span>
          <span style="background:#e9e9e9"></span><span style="background:#3aa2d8"></span><span style="background:#5a2a82"></span>
        </div>
        <div class="more">plus many more</div>
        <p>You may be able to receive rebates of up to <b>75% of your session costs</b> from CareShield or Private Health Insurers.</p>
        <div class="promo-bar teal">Click here for more details.
          <svg width="16" height="16" viewBox="0 0 16 16"><circle cx="8" cy="8" r="7" fill="#fff"/><path d="M6 4.5L9.5 8L6 11.5" fill="none" stroke="#2d8c96" stroke-width="2"/></svg></div>
      </a>
    </div>
  </div>
</section>

<footer class="site-footer">
  <div class="wrap footer-grid">
    <div>
      <h4>Newsletter Signup</h4>
      <div class="email">Email Address
        <svg width="14" height="10" viewBox="0 0 14 10"><rect x="0.5" y="0.5" width="13" height="9" fill="#333"/><path d="M1 1L7 6L13 1" fill="none" stroke="#fff" stroke-width="1.2"/></svg></div>
      <div class="social"><span></span><span></span><span></span><span></span></div>
    </div>
    <div>
      <h4>Links</h4>
      <ul class="links">
        <li>Home</li><li>Contact</li>
        <li>About</li><li>Counselling Types</li>
        <li>Resources</li><li>Relationship Counselling Locations</li>
        <li>Blog</li><li>Sex Theraphy Locations</li>
        <li>Shop</li><li>Quizzes</li>
        <li>Cart</li><li>FAQs</li>
      </ul>
    </div>
    <div class="contact">
      <h4>Contact Us</h4>
      <div><svg width="8" height="11" viewBox="0 0 8 11"><path d="M4 11C4 11 0 6 0 4A4 4 0 0 1 8 4C8 6 4 11 4 11Z" fill="#aaa"/><circle cx="4" cy="4" r="1.5" fill="#2f2f2f"/></svg><span>24 Building name, Street name,<br>City - Zipcode</span></div>
      <div><svg width="8" height="11" viewBox="0 0 8 11"><rect x="0.5" y="0.5" width="7" height="10" rx="1.5" fill="none" stroke="#aaa"/></svg><span>1300 555 019</span></div>
    </div>
    <div class="copy">Copyright © 2017<br>The Kelvale Clinic.<br>All rights reserved.</div>
  </div>
</footer>

</body>
</html>
```